UI Improvement for FlorKeep app

We are looking for a talented UI/UX designer to REFINE and enhance the visual design of our mobile application, FlorKeep. The app is fully functional, but we need a designer to improve its aesthetics by specifying design elements such as fonts, colors, spacing, and component styles.
Your task will be to analyze the CURRENT UI and provide detailed design specifications that will make the app more visually appealing, modern, and user-friendly.
TODO:
Review the existing FlorKeep app design (see attachments) and identify areas for visual improvement.
Provide a detailed UI style guide, including:
Typography (font choices, sizes, and weights)
Color palette (primary, secondary, and accent colors)
Component styling (buttons, forms, icons, and interactive elements)
Spacing and layout guidelines (margins, paddings, and alignment)
Ensure the design remains clean, modern, and professional while maintaining usability and accessibility.
Provide design mockups or visual examples (if possible) to illustrate the proposed changes.
Deliverables:
A UI Style Guide (PDF or Figma file) with specifications on fonts, colors, spacing, and UI components.
Optionally, before/after mockups or examples demonstrating the improvements.
Ideal Designer:
Strong experience in mobile UI/UX design.
Understanding of modern design trends and best practices.
Ability to communicate design choices clearly for easy developer implementation.
I have attached 7 images showcasing the main UI screens used in the FlorKeep app. These screens need visual enhancements to improve their overall look and user experience.
The images represent the current design in three key modes:
LIST Mode – Displays data in a structured list format.
READ Mode – Shows detailed information when a user selects an item.
ADD/EDIT Mode – Allows users to input or modify information.
Additionally, there is a ‘MORE’ page, which serves as a menu listing other features of the application.
Task Objective:
Please refine and improve these UIs to create a more modern, visually appealing, and user-friendly experience. Focus on typography, colors, spacing, and component styling to ensure a cohesive and polished design.
Look and feel
Each slider illustrates characteristics of the customer's brand and the style your logo design should communicate.

```html
<!DOCTYPE html>
<html lang="en">
<head>
<meta charset="utf-8">
<title>FlorKeep app – UI style guide</title>
<link href="https://fonts.googleapis.com/css2?family=Figtree:wght@400;500;600;700&family=Nunito+Sans:wght@400;600;700&family=Inter:wght@400;500;600&display=swap" rel="stylesheet">
<style>
:root{
  --blue:#1B7ECC;--ink:#1C1F34;--slate:#4B4B5A;--gray:#636669;--mute:#7C848B;
  --bg:#F2F6F7;--line:#E2E7F1;
  --cyan:#25C2E3;--green:#29BA85;--orange:#F77E53;--yellow:#FFBE0B;--pink:#FF5C75;--violet:#7859F4;
  --legacy-bg:#EDEDED;--legacy-nav:#F4F4F4;--legacy-yellow:#FFFDE1;--legacy-cyan:#E3FEFE;--legacy-green:#94EE8E;
  --font-head:'Figtree',sans-serif;--font-body:'Nunito Sans',sans-serif;--font-sys:'Inter',sans-serif;
}
*{box-sizing:border-box;margin:0;padding:0}
html,body{width:1200px;height:1085px;overflow:hidden;background:#fff}
body{position:relative;font-family:var(--font-head);color:var(--ink)}
svg.icon{display:inline-block;vertical-align:middle;flex:none}

.guide-title{position:absolute;left:50px;top:48px;font:700 36px/1 var(--font-head);letter-spacing:-.3px}
.section-label{position:absolute;top:106px;font:500 12px/1 var(--font-head);color:var(--mute)}
.swatches{position:absolute;left:49px;top:129px;display:grid;grid-template-columns:repeat(6,33px);column-gap:6.5px;row-gap:10px}
.swatch{width:33px;height:33px;border-radius:2px;display:flex;align-items:center;justify-content:center;font:400 6.5px var(--font-head);color:#fff}
.swatch.light{color:var(--slate)}
.swatch.row-start{grid-column:1}
.font-sample{position:absolute;left:329px;font:400 28px/1 var(--font-head);color:var(--ink)}
.font-sample.nunito{font-family:var(--font-body)}

.section-bar{position:absolute;left:49px;top:297px;width:1111px;height:30px;background:#000;color:#fff;font:700 11.5px/30px var(--font-head);padding-left:9px}

/* legacy screens */
.legacy{position:absolute;width:161px;height:346px;background:#fff;overflow:hidden;font-family:var(--font-sys)}
.legacy-status{height:20px;background:#000;color:#fff;display:flex;align-items:center;justify-content:space-between;padding:0 15px 0 24px;font:600 7px var(--font-sys)}
.legacy-status .sys{display:flex;gap:3px;align-items:center}
.legacy-nav{height:25px;background:var(--legacy-nav);display:flex;align-items:center;justify-content:space-between;padding:0 7px;font:400 7px var(--font-sys);color:#222}
.legacy-body{height:269px;background:var(--legacy-bg);overflow:hidden;display:flex;flex-direction:column;gap:3.4px;padding:1px 3px 0}
.legacy-row{flex:none;height:20px;background:#fff;display:flex;align-items:center;gap:2px;padding:0 3px;font-size:6px;color:#222}
.legacy-row .icon{color:var(--blue)}
.legacy-block{flex:none;padding:6px 3px 0;font-size:6px;color:#222;position:relative}
.legacy-block.yellow{background:var(--legacy-yellow);height:46px}
.legacy-block.cyan{background:var(--legacy-cyan)}
.legacy-block.green{background:var(--legacy-green)}
.legacy-block .block-head{display:flex;justify-content:space-between;font-weight:600}
.legacy-block .block-head span+span{font-weight:400;color:#bbb;font-size:5px}
.legacy-block .block-text{margin-top:11px;padding-right:14px;line-height:1.2}
.legacy-block .chev{position:absolute;right:5px;top:24px;color:#999}
.legacy-block .rule{height:1px;background:#ccc;margin:10px 0 6px}
.legacy-block .add{display:flex;align-items:center;gap:2px;padding-bottom:4px}
.legacy-block .add .icon{color:var(--blue)}
.legacy-card{flex:none;background:#fff;padding:4px 4px;font-size:6px;color:#222;position:relative}
.legacy-field{margin-bottom:4px}
.legacy-field .lbl{font-size:4.5px;color:var(--blue);line-height:1.1}
.legacy-field .val{line-height:1.15}
.legacy-card .menu{position:absolute;right:5px;top:7px}
.legacy-tabs{height:22px;display:flex;justify-content:space-around;padding:1px 0 0}
.legacy-tab{display:flex;flex-direction:column;align-items:center;gap:2px;font:400 4.5px var(--font-sys);color:#222;width:30px}
.legacy-tab.active{color:var(--blue)}
.home-bar{position:absolute;left:50%;transform:translateX(-50%);width:57px;height:2px;border-radius:2px;background:#555}
.legacy .home-bar{bottom:8px}

/* refreshed screens */
.phone{position:absolute;width:170px;border:5px solid #111;border-radius:27px;overflow:hidden;background:var(--bg)}
.hero{background:var(--blue);color:#fff;position:relative;padding:0 9px}
.status{height:26px;display:flex;align-items:center;justify-content:space-between;padding:4px 6px 0 13px;font:600 7px var(--font-sys)}
.status .sys{display:flex;gap:2.5px;align-items:center}
.notch{position:absolute;left:50%;top:4px;transform:translateX(-50%);width:52px;height:15px;border-radius:8px;background:#111}
.hero-nav{display:flex;justify-content:space-between;align-items:center;height:12px;margin-top:1px}
.hero-nav .actions{display:flex;gap:7px;align-items:center}
.hero-id{display:flex;gap:6px;align-items:flex-start;margin-top:4px}
.avatar{width:26px;height:26px;border-radius:50%;display:flex;align-items:center;justify-content:center;font:600 9px var(--font-head);color:#fff;flex:none;margin-top:3px}
.hero-kicker{font:400 6.5px var(--font-body);opacity:.95}
.hero-name{font:700 14.5px/1.13 var(--font-head);margin-top:1px}
.cards{display:flex;flex-direction:column;gap:4.7px;padding:0 7px;position:relative}
.card{background:#fff;border-radius:5px;padding:0 7px}
.card-head{display:flex;justify-content:space-between;align-items:center;height:22px;border-bottom:.6px solid var(--line);font:600 7px var(--font-head);color:var(--ink)}
.card-head .icon.faint{color:#D5D9DE}
.card-head .icon.accent{color:var(--blue)}
.card-add{display:flex;align-items:center;gap:3px;height:22px;font:400 7.5px var(--font-body);color:var(--blue)}
.card-text{font:400 7.2px/1.3 var(--font-body);color:var(--slate);padding:7px 0 8px;border-bottom:.6px solid var(--line)}
.card-text .dot{color:#B8BCC2;padding:0 2px;font-size:5px;vertical-align:middle}
.card-text.plain{border-bottom:0}
.fields{padding:6px 0 5px}
.field{margin-bottom:6.5px}
.field .lbl{font:400 5.3px var(--font-body);color:var(--mute)}
.field .val{font:400 7.3px/1.3 var(--font-body);color:var(--slate);margin-top:2px}
.field .val.active{color:var(--green)}
.phone .home-bar{position:static;transform:none;margin:0 auto;background:#111;width:55px;height:2.5px}
</style>
</head>
<body>

<svg width="0" height="0" style="position:absolute">
  <defs>
    <symbol id="i-plus" viewBox="0 0 10 10"><circle cx="5" cy="5" r="4.3" fill="none" stroke="currentColor" stroke-width=".9"/><path d="M5 2.8v4.4M2.8 5h4.4" stroke="currentColor" stroke-width=".9"/></symbol>
    <symbol id="i-back" viewBox="0 0 10 10"><path d="M9 5H1.5M5 1.5 1.5 5 5 8.5" fill="none" stroke="currentColor" stroke-width="1.1"/></symbol>
    <symbol id="i-dots" viewBox="0 0 10 4"><circle cx="1.5" cy="2" r="1" fill="currentColor"/><circle cx="5" cy="2" r="1" fill="currentColor"/><circle cx="8.5" cy="2" r="1" fill="currentColor"/></symbol>
    <symbol id="i-collapse" viewBox="0 0 8 10"><path d="M1.5 1.5 4 4 6.5 1.5M1.5 8.5 4 6 6.5 8.5" fill="none" stroke="currentColor" stroke-width=".9"/></symbol>
    <symbol id="i-expand" viewBox="0 0 8 10"><path d="M1.5 4 4 1.5 6.5 4M1.5 6 4 8.5 6.5 6" fill="none" stroke="currentColor" stroke-width=".9"/></symbol>
    <symbol id="i-chev" viewBox="0 0 10 6"><path d="M1 1l4 4 4-4" fill="none" stroke="currentColor" stroke-width=".8"/></symbol>
    <symbol id="i-person" viewBox="0 0 10 10"><circle cx="5" cy="3" r="2.2" fill="currentColor"/><path d="M1 10c0-3 2-4.5 4-4.5S9 7 9 10z" fill="currentColor"/></symbol>
    <symbol id="i-badge" viewBox="0 0 10 10"><rect x="2.5" y="0.5" width="5" height="2" rx=".5" fill="currentColor"/><circle cx="5" cy="4.3" r="1.8" fill="currentColor"/><path d="M1.5 10c0-2.5 1.6-3.5 3.5-3.5S8.5 7.5 8.5 10z" fill="currentColor"/></symbol>
    <symbol id="i-plane" viewBox="0 0 10 10"><path d="M9.5 5 6 4.2 4 .5H3l1 3.7-2.3-.3L.8 2.6H.2l.5 2.4-.5 2.4h.6l.9-1.3 2.3-.3-1 3.7h1L6 5.8z" fill="currentColor"/></symbol>
    <symbol id="i-request" viewBox="0 0 10 10"><path d="M3 1h1.5v4H6V2.5h1.3V5h.8V3.3h1.2v3.2c0 2-1.3 3-3.2 3H5C3.5 9.5 2 8 1.5 6.5l-.6-1.7 1.1-.3 1 1.6z" fill="currentColor"/></symbol>
    <symbol id="i-case" viewBox="0 0 10 10"><rect x=".8" y="3" width="8.4" height="6" rx="1" fill="currentColor"/><path d="M3.5 3V1.6h3V3" fill="none" stroke="currentColor" stroke-width=".9"/></symbol>
    <symbol id="i-print" viewBox="0 0 10 10"><rect x="2.5" y=".8" width="5" height="2.5" fill="none" stroke="currentColor" stroke-width=".9"/><rect x=".8" y="3.3" width="8.4" height="3.8" rx=".8" fill="none" stroke="currentColor" stroke-width=".9"/><rect x="2.5" y="6" width="5" height="3.2" fill="none" stroke="currentColor" stroke-width=".9"/></symbol>
    <symbol id="i-list" viewBox="0 0 10 10"><path d="M2 2h6M2 5h6M2 8h6" stroke="currentColor" stroke-width="1"/></symbol>
    <symbol id="i-signal" viewBox="0 0 12 8"><rect x="0" y="5.5" width="2" height="2.5" fill="currentColor"/><rect x="3.3" y="4" width="2" height="4" fill="currentColor"/><rect x="6.6" y="2" width="2" height="6" fill="currentColor"/><rect x="9.9" y="0" width="2" height="8" fill="currentColor"/></symbol>
    <symbol id="i-wifi" viewBox="0 0 12 9"><path d="M6 8.5 4.3 6.7a2.5 2.5 0 0 1 3.4 0zM2.6 5a4.9 4.9 0 0 1 6.8 0l-1.1 1.1a3.3 3.3 0 0 0-4.6 0zM.8 3.2a7.5 7.5 0 0 1 10.4 0L10.1 4.3a5.9 5.9 0 0 0-8.2 0z" fill="currentColor"/></symbol>
    <symbol id="i-batt" viewBox="0 0 18 9"><rect x=".5" y=".5" width="15" height="8" rx="2" fill="none" stroke="currentColor" stroke-opacity=".5"/><rect x="2" y="2" width="12" height="5" rx="1" fill="currentColor"/><rect x="16.3" y="3" width="1.2" height="3" rx=".5" fill="currentColor" fill-opacity=".5"/></symbol>
  </defs>
</svg>

<h1 class="guide-title">FlorKeep app</h1>

<p class="section-label" style="left:50px">Colors</p>
<div class="swatches">
  <div class="swatch" style="background:var(--blue)">1B7ECC</div>
  <div class="swatch" style="background:var(--ink)">1C1F34</div>
  <div class="swatch" style="background:var(--slate)">4B4B5A</div>
  <div class="swatch" style="background:var(--gray)">636669</div>
  <div class="swatch" style="background:var(--mute)">7C848B</div>
  <div></div>
  <div class="swatch light" style="background:var(--bg)">F2F6F7</div>
  <div class="swatch light" style="background:var(--line)">E2E7F1</div>
  <div></div><div></div><div></div><div></div>
  <div class="swatch" style="background:var(--cyan)">25C2E3</div>
  <div class="swatch" style="background:var(--green)">29BA85</div>
  <div class="swatch" style="background:var(--orange)">F77E53</div>
  <div class="swatch" style="background:var(--yellow)">FFBE0B</div>
  <div class="swatch" style="background:var(--pink)">FF5C75</div>
  <div class="swatch" style="background:var(--violet)">7859F4</div>
</div>

<p class="section-label" style="left:329px">Fonts</p>
<p class="font-sample" style="top:132px">Figtree</p>
<p class="font-sample nunito" style="top:175px">Nunito Sans</p>

<div class="section-bar">Read Page</div>

<!-- Legacy contact screen, upper part -->
<section class="legacy" style="left:49px;top:344px">
  <div class="legacy-status"><span>3:13</span><span class="sys"><svg class="icon" width="8" height="5"><use href="#i-dots"/></svg><svg class="icon" width="8" height="6"><use href="#i-wifi"/></svg><svg class="icon" width="12" height="6"><use href="#i-batt"/></svg></span></div>
  <div class="legacy-nav"><svg class="icon" width="8" height="8"><use href="#i-back"/></svg><span>Contact</span><svg class="icon" width="7" height="3"><use href="#i-dots"/></svg></div>
  <div class="legacy-body">
    <div class="legacy-row" style="height:19px"><svg class="icon" width="6.5" height="6.5"><use href="#i-plus"/></svg>Add Email -e</div>
    <div class="legacy-row"><svg class="icon" width="6.5" height="6.5"><use href="#i-plus"/></svg>Add Social Media -e</div>
    <div class="legacy-row"><svg class="icon" width="6.5" height="6.5"><use href="#i-plus"/></svg>Add Emergency Contact -e</div>
    <div class="legacy-row"><svg class="icon" width="6.5" height="6.5"><use href="#i-plus"/></svg>Add Personal Information -e</div>
    <div class="legacy-row"><svg class="icon" width="6.5" height="6.5"><use href="#i-plus"/></svg>Add Work Info -e</div>
    <div class="legacy-row"><svg class="icon" width="6.5" height="6.5"><use href="#i-plus"/></svg>Add Skills/Talents -e</div>
    <div class="legacy-row"><svg class="icon" width="6.5" height="6.5"><use href="#i-plus"/></svg>Add Resources -e</div>
    <div class="legacy-block yellow"><div class="block-head"><span>Pilots -e</span><span>Collapse</span></div><p class="block-text">Marlow, Jenna, 3647946, 10/31/23</p><svg class="icon chev" width="6" height="4"><use href="#i-chev"/></svg></div>
    <div class="legacy-block cyan"><div class="block-head"><span>Aircraft Owner -e</span><span>Collapse</span></div><p class="block-text">Personal: Marlow, Jenna: Skylark: 210: Skylark Aircraft Company, Single Engine, 1100</p><svg class="icon chev" width="6" height="4"><use href="#i-chev"/></svg><div class="rule"></div><div class="add"><svg class="icon" width="6.5" height="6.5"><use href="#i-plus"/></svg>Add Aircraft Owner -e</div></div>
  </div>
  <nav class="legacy-tabs">
    <span class="legacy-tab active"><svg class="icon" width="6" height="6"><use href="#i-person"/></svg>Contact</span>
    <span class="legacy-tab"><svg class="icon" width="6" height="6"><use href="#i-badge"/></svg>Pilot</span>
    <span class="legacy-tab"><svg class="icon" width="6" height="6"><use href="#i-plane"/></svg>Plane</span>
    <span class="legacy-tab"><svg class="icon" width="6" height="6"><use href="#i-request"/></svg>Flt Request</span>
    <span class="legacy-tab"><svg class="icon" width="6" height="3"><use href="#i-dots"/></svg>More</span>
  </nav>
  <div class="home-bar"></div>
</section>

<!-- Legacy contact screen, lower part -->
<section class="legacy" style="left:49px;top:696px;height:348px">
  <div class="legacy-status"><span>3:14</span><span class="sys"><svg class="icon" width="8" height="5"><use href="#i-dots"/></svg><svg class="icon" width="8" height="6"><use href="#i-wifi"/></svg><svg class="icon" width="12" height="6"><use href="#i-batt"/></svg></span></div>
  <div class="legacy-nav"><svg class="icon" width="8" height="8"><use href="#i-back"/></svg><span>Contact</span><svg class="icon" width="7" height="3"><use href="#i-dots"/></svg></div>
  <div class="legacy-body" style="height:271px">
    <div class="legacy-row" style="height:14px"><svg class="icon" width="6.5" height="6.5"><use href="#i-plus"/></svg>Add Personal Information -e</div>
    <div class="legacy-row"><svg class="icon" width="6.5" height="6.5"><use href="#i-plus"/></svg>Add Work Info -e</div>
    <div class="legacy-row"><svg class="icon" width="6.5" height="6.5"><use href="#i-plus"/></svg>Add Skills/Talents -e</div>
    <div class="legacy-row"><svg class="icon" width="6.5" height="6.5"><use href="#i-plus"/></svg>Add Resources -e</div>
    <div class="legacy-block yellow"><div class="block-head"><span>Pilots -e</span><span>Collapse</span></div><p class="block-text">Marlow, Jenna, 3647946, 10/31/23</p><svg class="icon chev" width="6" height="4"><use href="#i-chev"/></svg></div>
    <div class="legacy-block cyan"><div class="block-head"><span>Aircraft Owner -e</span><span>Collapse</span></div><p class="block-text">Personal: Marlow, Jenna: Skylark: 210: Skylark Aircraft Company, Single Engine, 1100</p><svg class="icon chev" width="6" height="4"><use href="#i-chev"/></svg><div class="rule"></div><div class="add"><svg class="icon" width="6.5" height="6.5"><use href="#i-plus"/></svg>Add Aircraft Owner -e</div></div>
    <div class="legacy-block green"><div class="block-head"><span>Qualified Pilot -e</span><span>Collapse</span></div><p class="block-text">Marlow, Jenna: Skylark: 210: Skylark Aircraft Company, Single Engine, 1100</p><svg class="icon chev" width="6" height="4"><use href="#i-chev"/></svg><div class="rule"></div><div class="add"><svg class="icon" width="6.5" height="6.5"><use href="#i-plus"/></svg>Add Qualified Pilot -e</div></div>
  </div>
  <nav class="legacy-tabs">
    <span class="legacy-tab active"><svg class="icon" width="6" height="6"><use href="#i-person"/></svg>Contact</span>
    <span class="legacy-tab"><svg class="icon" width="6" height="6"><use href="#i-badge"/></svg>Pilot</span>
    <span class="legacy-tab"><svg class="icon" width="6" height="6"><use href="#i-plane"/></svg>Plane</span>
    <span class="legacy-tab"><svg class="icon" width="6" height="6"><use href="#i-request"/></svg>Flt Request</span>
    <span class="legacy-tab"><svg class="icon" width="6" height="3"><use href="#i-dots"/></svg>More</span>
  </nav>
  <div class="home-bar"></div>
</section>

<!-- Refreshed contact screen -->
<section class="phone" style="left:221px;top:339px;height:655px">
  <header class="hero" style="height:91px">
    <div class="notch"></div>
    <div class="status"><span>9:41</span><span class="sys"><svg class="icon" width="8" height="5.5"><use href="#i-signal"/></svg><svg class="icon" width="7.5" height="5.5"><use href="#i-wifi"/></svg><svg class="icon" width="11" height="5.5"><use href="#i-batt"/></svg></span></div>
    <div class="hero-nav"><svg class="icon" width="8" height="8"><use href="#i-back"/></svg><svg class="icon" width="8" height="3.5"><use href="#i-dots"/></svg></div>
    <div class="hero-id">
      <div class="avatar" style="background:var(--green)">MJ</div>
      <div><p class="hero-kicker">Contact</p><p class="hero-name">Marlow, Jenna</p></div>
    </div>
  </header>
  <div class="cards" style="margin-top:-17px">
    <div class="card"><div class="card-head">Email<svg class="icon faint" width="5" height="7"><use href="#i-expand"/></svg></div><div class="card-add"><svg class="icon" width="8" height="8"><use href="#i-plus"/></svg>Add</div></div>
    <div class="card"><div class="card-head">Social Media<svg class="icon faint" width="5" height="7"><use href="#i-expand"/></svg></div><div class="card-add"><svg class="icon" width="8" height="8"><use href="#i-plus"/></svg>Add</div></div>
    <div class="card"><div class="card-head">Emergency Contact<svg class="icon faint" width="5" height="7"><use href="#i-expand"/></svg></div><div class="card-add"><svg class="icon" width="8" height="8"><use href="#i-plus"/></svg>Add</div></div>
    <div class="card"><div class="card-head">Personal Information<svg class="icon faint" width="5" height="7"><use href="#i-expand"/></svg></div><div class="card-add"><svg class="icon" width="8" height="8"><use href="#i-plus"/></svg>Add</div></div>
    <div class="card"><div class="card-head">Work Info<svg class="icon faint" width="5" height="7"><use href="#i-expand"/></svg></div><div class="card-add"><svg class="icon" width="8" height="8"><use href="#i-plus"/></svg>Add</div></div>
    <div class="card"><div class="card-head">Skills/Talents<svg class="icon faint" width="5" height="7"><use href="#i-expand"/></svg></div><div class="card-add"><svg class="icon" width="8" height="8"><use href="#i-plus"/></svg>Add</div></div>
    <div class="card"><div class="card-head">Resources<svg class="icon faint" width="5" height="7"><use href="#i-expand"/></svg></div><div class="card-add"><svg class="icon" width="8" height="8"><use href="#i-plus"/></svg>Add</div></div>
    <div class="card"><div class="card-head">Pilots<svg class="icon accent" width="5" height="7"><use href="#i-collapse"/></svg></div><p class="card-text plain">Marlow, Jenna<span class="dot">●</span>3647946<span class="dot">●</span>0/31/23</p></div>
    <div class="card"><div class="card-head">Aircraft Owner<svg class="icon accent" width="5" height="7"><use href="#i-collapse"/></svg></div><p class="card-text">Personal<span class="dot">●</span>Marlow, Jenna<span class="dot">●</span>Skylark-210<span class="dot">●</span>Skylark Aircraft Company<span class="dot">●</span>Single Engine, 1100</p><div class="card-add"><svg class="icon" width="8" height="8"><use href="#i-plus"/></svg>Add</div></div>
    <div class="card"><div class="card-head">Qualified Pilot<svg class="icon accent" width="5" height="7"><use href="#i-collapse"/></svg></div><p class="card-text">Marlow, Jenna<span class="dot">●</span>Skylark-210<span class="dot">●</span>Skylark Aircraft Company<span class="dot">●</span>Single Engine, 1100</p><div class="card-add"><svg class="icon" width="8" height="8"><use href="#i-plus"/></svg>Add</div></div>
  </div>
  <div style="padding-top:17px"><div class="home-bar"></div></div>
</section>

<!-- Legacy pilot screen -->
<section class="legacy" style="left:436px;top:344px;width:160px">
  <div class="legacy-status"><span>3:17</span><span class="sys"><svg class="icon" width="8" height="5"><use href="#i-dots"/></svg><svg class="icon" width="8" height="6"><use href="#i-wifi"/></svg><svg class="icon" width="12" height="6"><use href="#i-batt"/></svg></span></div>
  <div class="legacy-nav"><svg class="icon" width="8" height="8"><use href="#i-back"/></svg><span>Pilot</span><svg class="icon" width="7" height="3"><use href="#i-dots"/></svg></div>
  <div class="legacy-body">
    <div class="legacy-card" style="height:110px">
      <svg class="icon menu" width="6" height="3"><use href="#i-dots"/></svg>
      <div class="legacy-field"><p class="lbl">Pilot -e</p><p class="val">Dorsey, Wade, Elliot</p></div>
      <div class="legacy-field"><p class="lbl">Pilot Certificate No -e</p><p class="val">3182133</p></div>
      <div class="legacy-field" style="padding-left:45px"><p class="lbl">Medical Expiration Date -e</p><p class="val">9/30/24</p></div>
      <div class="legacy-field"><p class="lbl">Flight Review Expiration Date -e</p><p class="val">6/30/24</p></div>
      <div class="legacy-field"><p class="lbl">Total Flight Time -e</p><p class="val">2500</p></div>
    </div>
    <div class="legacy-card" style="padding:6px 14px 4px 4px;height:65px;line-height:1.2">
      <svg class="icon" width="6" height="4" style="position:absolute;right:4px;top:8px;color:#999"><use href="#i-chev"/></svg>
      <p>P12, Pine Hollow Airport, Pine Hollow, FL, 32190, 11, 2500</p>
      <div style="height:1px;background:#ddd;margin:9px -10px 8px 0"></div>
      <svg class="icon" width="6" height="4" style="position:absolute;right:4px;top:39px;color:#999"><use href="#i-chev"/></svg>
      <p>M41, Mesa Ridge Municipal Airport, Mesa Ridge, CO, 80920, 5,334 ft, 4,800 ft</p>
    </div>
    <div class="legacy-row"><svg class="icon" width="6.5" height="6.5"><use href="#i-plus"/></svg>Add Base Airport -e</div>
    <div class="legacy-row"><svg class="icon" width="6.5" height="6.5"><use href="#i-plus"/></svg>Add Ratings -e</div>
    <div class="legacy-card" style="height:60px">
      <svg class="icon menu" width="6" height="3"><use href="#i-dots"/></svg>
      <div class="legacy-field"><p class="lbl">Contact -e</p><p class="val">Tessa Dorsey</p></div>
      <div class="legacy-field"><p class="lbl">Phone -e</p><p class="val">555-014-2290</p></div>
      <div class="legacy-field"><p class="lbl">Relationship -e</p></div>
    </div>
  </div>
  <nav class="legacy-tabs">
    <span class="legacy-tab"><svg class="icon" width="6" height="6"><use href="#i-person"/></svg>Contact</span>
    <span class="legacy-tab active"><svg class="icon" width="6" height="6"><use href="#i-badge"/></svg>Pilot</span>
    <span class="legacy-tab"><svg class="icon" width="6" height="6"><use href="#i-plane"/></svg>Plane</span>
    <span class="legacy-tab"><svg class="icon" width="6" height="6"><use href="#i-request"/></svg>Flt Request</span>
    <span class="legacy-tab"><svg class="icon" width="6" height="3"><use href="#i-dots"/></svg>More</span>
  </nav>
  <div class="home-bar"></div>
</section>

<!-- Refreshed pilot screen -->
<section class="phone" style="left:608px;top:339px;height:534px">
  <header class="hero" style="height:108px">
    <div class="notch"></div>
    <div class="status"><span>9:41</span><span class="sys"><svg class="icon" width="8" height="5.5"><use href="#i-signal"/></svg><svg class="icon" width="7.5" height="5.5"><use href="#i-wifi"/></svg><svg class="icon" width="11" height="5.5"><use href="#i-batt"/></svg></span></div>
    <div class="hero-nav"><svg class="icon" width="8" height="8"><use href="#i-back"/></svg><svg class="icon" width="8" height="3.5"><use href="#i-dots"/></svg></div>
    <div class="hero-id">
      <div class="avatar" style="background:var(--cyan);font-size:8.5px">DWE</div>
      <div><p class="hero-kicker">Pilot</p><p class="hero-name">Dorsey, Wade,<br>Elliot</p></div>
    </div>
  </header>
  <div class="cards" style="margin-top:-17px">
    <div class="card" style="height:146px"><div class="card-head">Pilot Information<svg class="icon accent" width="8" height="3.5"><use href="#i-dots"/></svg></div>
      <div class="fields">
        <div class="field"><p class="lbl">Pilot Name</p><p class="val">Dorsey, Wade, Elliot</p></div>
        <div class="field"><p class="lbl">Pilot Certification Number</p><p class="val">3182133</p></div>
        <div class="field"><p class="lbl">Medical Expiration Date</p><p class="val">9/30/24</p></div>
        <div class="field"><p class="lbl">Flight Review Expiration Date</p><p class="val">6/30/24</p></div>
        <div class="field"><p class="lbl">Total Flight Time</p><p class="val">2500</p></div>
      </div>
    </div>
    <div class="card"><div class="card-head">Base Airport<svg class="icon accent" width="5" height="7"><use href="#i-collapse"/></svg></div>
      <p class="card-text" style="padding-top:9px">P12<span class="dot">●</span>Pine Hollow Airport<span class="dot">●</span>Pine Hollow, FL, 32190<span class="dot">●</span>11, 2500</p>
      <p class="card-text">M41<span class="dot">●</span>Mesa Ridge Airport<span class="dot">●</span>Mesa Ridge, CO, 80920<span class="dot">●</span>5,334 ft, 4,800 ft</p>
      <div class="card-add"><svg class="icon" width="8" height="8"><use href="#i-plus"/></svg>Add</div>
    </div>
    <div class="card"><div class="card-head">Ratings<svg class="icon faint" width="5" height="7"><use href="#i-expand"/></svg></div><div class="card-add"><svg class="icon" width="8" height="8"><use href="#i-plus"/></svg>Add</div></div>
    <div class="card" style="height:100px"><div class="card-head">Contact Information<svg class="icon accent" width="8" height="3.5"><use href="#i-dots"/></svg></div>
      <div class="fields">
        <div class="field"><p class="lbl">Contact Name</p><p class="val">Tessa Dorsey</p></div>
        <div class="field"><p class="lbl">Phone</p><p class="val">555-014-2290</p></div>
        <div class="field"><p class="lbl">Relationship</p><p class="val">Brother</p></div>
      </div>
    </div>
  </div>
  <div style="padding-top:14px"><div class="home-bar"></div></div>
</section>

<!-- Legacy work order screen -->
<section class="legacy" style="left:823px;top:344px;width:160px">
  <div class="legacy-status"><span>2:16</span><span class="sys"><svg class="icon" width="8" height="5"><use href="#i-dots"/></svg><svg class="icon" width="8" height="6"><use href="#i-wifi"/></svg><svg class="icon" width="12" height="6"><use href="#i-batt"/></svg></span></div>
  <div class="legacy-nav"><svg class="icon" width="8" height="8"><use href="#i-back"/></svg><span>WorkOrder</span><svg class="icon" width="7" height="3"><use href="#i-dots"/></svg></div>
  <div class="legacy-body" style="background:#D9D9D9">
    <div class="legacy-card" style="height:23px;display:flex;gap:5px;padding:2px 5px">
      <span style="width:17px;height:18px;border:.5px solid #ccc;border-radius:3px;display:flex;flex-direction:column;align-items:center;justify-content:center;gap:2px;font-size:3.5px"><svg class="icon" width="4" height="4"><use href="#i-list"/></svg>Print</span>
      <span style="width:17px;height:18px;border:.5px solid #ccc;border-radius:3px;display:flex;flex-direction:column;align-items:center;justify-content:center;gap:2px;font-size:3.5px"><svg class="icon" width="4" height="4"><use href="#i-list"/></svg>Create...</span>
      <span style="width:17px;height:18px;border:.5px solid #ccc;border-radius:3px;display:flex;flex-direction:column;align-items:center;justify-content:center;gap:2px;font-size:3.5px"><svg class="icon" width="4" height="4"><use href="#i-list"/></svg>Create...</span>
    </div>
    <div class="legacy-card" style="height:146px">
      <svg class="icon menu" width="6" height="3"><use href="#i-dots"/></svg>
      <div class="legacy-field"><p class="lbl">Customer -e</p><p class="val">Farid , Omar</p></div>
      <div class="legacy-field" style="margin-bottom:0"><p class="lbl">Service Location -e</p><p class="val">Billing, 418 Willow Crest Lane , Ashford : TX, 78990</p></div>
      <div class="legacy-field" style="margin-bottom:0"><p class="lbl">Billing Address -e</p><p class="val">Billing, 418 Willow Crest Lane , Ashford : TX, 78990</p></div>
      <div class="legacy-field"><p class="lbl">Description -e</p><p class="val">Pool maintenance</p></div>
      <div class="legacy-field"><p class="lbl">Work Order Type -e</p><p class="val">One off job -e</p></div>
      <div class="legacy-field"><p class="lbl">WO Status -e</p><p class="val">Active -e</p></div>
      <div class="legacy-field"><p class="lbl">Billing Frequency -e</p><p class="val">Upon job completion -e</p></div>
    </div>
    <div class="legacy-row"><svg class="icon" width="6.5" height="6.5"><use href="#i-plus"/></svg>Add Technician -e</div>
    <div class="legacy-row"><svg class="icon" width="6.5" height="6.5"><use href="#i-plus"/></svg>Add Line Items -e</div>
  </div>
  <nav class="legacy-tabs">
    <span class="legacy-tab"><svg class="icon" width="6" height="6"><use href="#i-person"/></svg>Contact</span>
    <span class="legacy-tab"><svg class="icon" width="6" height="6"><use href="#i-badge"/></svg>Quote</span>
    <span class="legacy-tab active"><svg class="icon" width="6" height="6"><use href="#i-case"/></svg>WorkOrder</span>
    <span class="legacy-tab"><svg class="icon" width="6" height="6"><use href="#i-badge"/></svg>Invoice</span>
    <span class="legacy-tab"><svg class="icon" width="6" height="3"><use href="#i-dots"/></svg>More</span>
  </nav>
  <div class="home-bar"></div>
</section>

<!-- Refreshed work order screen -->
<section class="phone" style="left:994px;top:339px;height:415px">
  <header class="hero" style="height:91px">
    <div class="notch"></div>
    <div class="status"><span>9:41</span><span class="sys"><svg class="icon" width="8" height="5.5"><use href="#i-signal"/></svg><svg class="icon" width="7.5" height="5.5"><use href="#i-wifi"/></svg><svg class="icon" width="11" height="5.5"><use href="#i-batt"/></svg></span></div>
    <div class="hero-nav"><svg class="icon" width="8" height="8"><use href="#i-back"/></svg><span class="actions"><svg class="icon" width="8" height="8"><use href="#i-print"/></svg><svg class="icon" width="8" height="3.5"><use href="#i-dots"/></svg></span></div>
    <p class="hero-kicker" style="margin-top:9px">Work Order</p>
    <p class="hero-name" style="font-size:14px">12345ABC</p>
  </header>
  <div class="cards" style="margin-top:-17px">
    <div class="card" style="height:213px"><div class="card-head">Work Order Information<svg class="icon accent" width="8" height="3.5"><use href="#i-dots"/></svg></div>
      <div class="fields">
        <div class="field"><p class="lbl">Customer Name</p><p class="val">Farid, Omar</p></div>
        <div class="field"><p class="lbl">Service Location</p><p class="val">Billing, 418 Willow Crest Lane, Ashford, TX, 78990</p></div>
        <div class="field"><p class="lbl">Billing Address</p><p class="val">Billing, 418 Willow Crest Lane, Ashford, TX, 78990</p></div>
        <div class="field"><p class="lbl">Description</p><p class="val">Pool maintenance</p></div>
        <div class="field"><p class="lbl">Work Order Type</p><p class="val">One off job</p></div>
        <div class="field"><p class="lbl">Work Order Status</p><p class="val active">Active</p></div>
        <div class="field"><p class="lbl">Billing Frequency</p><p class="val">Upon job completion</p></div>
      </div>
    </div>
    <div class="card"><div class="card-head">Technician<svg class="icon faint" width="5" height="7"><use href="#i-expand"/></svg></div><div class="card-add"><svg class="icon" width="8" height="8"><use href="#i-plus"/></svg>Add</div></div>
    <div class="card"><div class="card-head">Line Items<svg class="icon faint" width="5" height="7"><use href="#i-expand"/></svg></div><div class="card-add"><svg class="icon" width="8" height="8"><use href="#i-plus"/></svg>Add</div></div>
  </div>
  <div style="padding-top:15px"><div class="home-bar"></div></div>
</section>

</body>
</html>
```